Wordpress Design Project for Bankruptcy Law Office in San Francisco

our current website: www.dorvanelilaw-example.com

we would like to re-design it for wordpress to make it faster and a bit more modern.

content should be similar to what we have there right now but also we do family law

please include logo for law office:

Law Office of Marta K. Dolvenidze

Thank you.
Updates

please see attached word document with logos that we like as an example.

we do tend to like color red.  darker red.

Please submit your design variations and logo as soon as possible.   We would like to go over them and make our decision

Reason: Please create couple of more variations of logo for your design, so we can make our decision what we like the most. Please see word doc for samples: Text: Law Office Of Marta K. Dolvenidze

Reason: final touches

Target Market(s)

bankruptcy and family law clients

Industry/Entity Type

Family Law

Requirements
Must have
• see examples of law sites
http://promo.lexorbin-example.com/testimonials

- new logo: Law Office of Marta K. Dolvenidze
- client intake form
- blog
- contact us form

Nice to have
• - map
- red color
- on the front page a nice photo of SF or a happy family

```html
<!DOCTYPE html>
<html lang="en">
<head>
<meta charset="utf-8">
<title>Law Office of Marta K. Dolvenidze</title>
<link rel="stylesheet" href="https://fonts.googleapis.com/css2?family=Open+Sans:wght@400;600;700&family=Arimo:wght@400;700&family=Crimson+Text:wght@400&display=swap">
<style>
:root{
  --admin:#232323;
  --admin-text:#d8d8d8;
  --logo-red:#b3161c;
  --white:#ffffff;
  --nav:#111111;
  --green:#7cb518;
  --green-dark:#5f9410;
  --text:#5b5b5b;
  --heading:#3a3a3a;
  --social:#3b8fd6;
  --social-light:#5cb4e8;
  --footer:#efefef;
  --line:#d6d6d6;
  --link:#2a7ab8;
}
*{box-sizing:border-box;margin:0;padding:0}
html,body{width:1200px;height:2412px;overflow:hidden}
body{position:relative;font-family:"Open Sans",Arial,sans-serif;color:var(--text);background:var(--footer)}
.abs{position:absolute}

.admin-bar{left:0;top:0;width:1200px;height:32px;background:var(--admin);color:var(--admin-text);font-size:14px;display:flex;align-items:center;padding:0 16px;gap:30px}
.admin-bar .right{margin-left:auto;display:flex;align-items:center;gap:8px}
.admin-bar .avatar{width:18px;height:18px;background:#888}

.header{left:0;top:32px;width:1200px;height:640px;background:linear-gradient(90deg,#3b1c0f,#5a2c16 20%,#3e1d0e 45%,#5e3019 70%,#3a1b0d)}
.content-wood{left:0;top:672px;width:1200px;height:1080px;background:linear-gradient(90deg,#4b2413,#6a361d 18%,#4a2312 40%,#6b381f 62%,#4d2614 82%,#643219)}

.logo{left:50px;top:58px;width:400px;height:80px;display:flex;align-items:center;gap:14px;font-weight:700;font-size:28px;color:var(--logo-red);line-height:1.2}
.logo .mark{width:20px;height:20px;background:var(--logo-red);flex:none}

.call{left:458px;top:36px;color:var(--white);font-family:"Arimo",Arial,sans-serif;font-size:54px;line-height:68px}
.call .phone{display:block;margin-top:20px;font-size:56px}

.header-btn{left:830px;top:60px;width:306px;height:46px;background:#000;border:2px solid var(--white);border-radius:8px;color:var(--white);font-weight:700;font-size:15px;padding:12px 22px}

.social-tab{left:1140px;width:60px;background:var(--social);border-radius:6px 0 0 6px;display:flex;align-items:center;justify-content:center}
.social-tab span{writing-mode:vertical-rl;transform:rotate(180deg);color:var(--white);font-weight:700;font-size:24px}
.tab-one{top:80px;height:178px}
.tab-two{top:262px;height:182px;background:var(--social-light)}

.main-nav{left:40px;top:204px;width:1100px;height:56px;background:linear-gradient(#2a2a2a,var(--nav));display:flex;align-items:center;padding-left:16px}
.main-nav a{color:var(--white);text-decoration:none;font-weight:700;font-size:15px;font-family:"Arimo",Arial,sans-serif;margin-right:34px;position:relative}
.main-nav a.has-sub::after{content:"";position:absolute;right:-20px;top:-12px;width:12px;height:12px;background:var(--white);border:1px solid #999}

.slider{left:44px;top:298px;width:1110px;height:290px;background:linear-gradient(160deg,#b7a48a,#6e5a44 45%,#2d241b 75%,#5a4837);border:4px solid #ddd}
.slide-caption{left:118px;top:326px;width:1036px;height:218px;background:rgba(95,50,25,.78);color:var(--white);font-family:"Crimson Text",Georgia,serif;font-size:50px;line-height:52px;padding:22px 120px 0 96px}

.dots{left:502px;top:624px;display:flex;gap:7px;align-items:center}
.dots i{width:12px;height:12px;border-radius:50%;background:#bbb;display:block;border:1px solid #999}
.dots i.active{background:#eee}
.dots b{width:24px;height:24px;border-radius:50%;background:#9a9a9a;display:flex;align-items:center;justify-content:center;color:#fff;font-size:13px}

.bar-title{left:40px;background:var(--white);border-radius:3px;height:30px;color:var(--heading);font-size:20px;padding:2px 12px;width:1114px}
.welcome-icon{left:40px;top:712px}
.welcome-title{top:712px;left:90px;width:1064px}
.text-box{left:40px;width:1114px;background:var(--white);border-radius:3px;font-size:15px;padding:4px 8px}
.welcome-text{top:756px;height:196px;line-height:27px}

.rule{left:40px;width:1114px;height:2px;background:rgba(255,255,255,.35)}

.card{top:1026px;width:262px;height:364px;background:var(--white);border-radius:4px;padding:28px 30px}
.card h3{font-size:13px;letter-spacing:2px;font-weight:700;color:var(--heading);text-transform:uppercase;line-height:20px;margin-bottom:4px}
.card p{font-size:14px;line-height:21px;border:1px solid #eee;padding:2px 4px}
.btn{display:inline-block;background:linear-gradient(var(--green),var(--green-dark));color:var(--white);font-size:12px;font-weight:700;padding:16px 20px;border-radius:2px;text-transform:uppercase}
.card .btn{position:absolute;left:30px}

.testi-label{left:40px;top:1474px;font-size:12px;letter-spacing:3px;color:#7a4a30;font-weight:700}
.testi-title{top:1504px;height:28px;font-size:15px}
.testi-text{top:1548px;height:172px;line-height:27px}

.disclaimer{left:40px;top:1790px;width:262px;background:var(--white);font-size:14px;line-height:29px;padding:6px 6px}
.foot-h{font-size:13px;letter-spacing:2px;font-weight:700;color:var(--heading);text-transform:uppercase}
.posts{left:324px;top:1790px;width:262px}
.post{background:var(--white);font-size:14px;line-height:23px;padding:8px 4px;margin-top:14px;border-bottom:1px solid var(--line)}
.post a{color:var(--link);text-decoration:none}
.post small{display:block;color:#999;font-size:11px}
.follow{background:var(--white);color:var(--green);font-size:14px;padding:4px 4px;margin-top:20px;border:1px solid var(--line)}
.contact{left:610px;top:1790px;width:460px;font-size:14px}
.contact label{display:block;line-height:20px;margin-top:6px}
.contact .field{width:254px;height:26px;background:var(--white);border:1px solid #9a9a9a}
.contact .area{width:454px;height:226px;background:var(--white);border:1px solid #9a9a9a}
.contact .btn{margin-top:18px;padding:12px 16px;font-size:11px}
.copyright{left:40px;top:2350px;font-size:13px;color:#888}
</style>
</head>
<body>

<div class="abs admin-bar">
  <span>Law Office of Marta K. Dolvenidze</span>
  <span>⟳ 1</span>
  <span>+ New</span>
  <span>Edit Page</span>
  <span class="right">Howdy, siteadmin <i class="avatar"></i></span>
</div>

<div class="abs header"></div>
<div class="abs content-wood"></div>

<div class="abs logo"><i class="mark"></i><span>Law Office of<br>Marta K. Dolvenidze</span></div>

<div class="abs call">Call us at<span class="phone">415-555-0187</span></div>
<div class="abs header-btn">Contact Us</div>

<div class="abs social-tab tab-one"><span>Friendwall</span></div>
<div class="abs social-tab tab-two"><span>Chirpline</span></div>

<nav class="abs main-nav">
  <a class="has-sub">About</a>
  <a class="has-sub">Areas of Practice</a>
  <a class="has-sub">Resources</a>
  <a>Blog</a>
  <a class="has-sub">FAQ</a>
  <a class="has-sub">Contact Us</a>
</nav>

<div class="abs slider" role="img" aria-label="Photo of a law office desk with an open book"></div>
<div class="abs slide-caption">The Law Office of Marta K. Dolvenidze is committed to providing quality legal services to those less privileged.</div>

<div class="abs dots"><b>‹</b><i></i><i class="active"></i><i></i><i></i><i></i><i></i><b>›</b></div>

<svg class="abs welcome-icon" width="40" height="30" viewBox="0 0 40 30" aria-hidden="true">
  <path d="M4 6 L14 2 L26 6 L36 2 V24 L26 28 L14 24 L4 28 Z M14 2 V24 M26 6 V28" fill="none" stroke="#d7b23a" stroke-width="2.5" stroke-linejoin="round"/>
</svg>
<div class="abs bar-title welcome-title">WELCOME TO BK LAW DESK – COMPLETE BANKRUPTCY INFORMATION</div>
<div class="abs text-box welcome-text">The Law Offices of Marta K. Dolvenidze is a consumer law office dedicated to consumer protection and zealously defending the rights of our clients. We offer the big firm quality legal representation with a small firm individualized attention to each client. Our office offers services in: all types of consumer bankruptcy filings, i.e. Chapter 7, Chapter 13, Chapter 11, negotiating a settlement of your debts, assisting you in the defense of collection litigation and defending you against foreclosure. Please review our site and see what we may be able to offer you. Feel free to call us at (415) 555-0187 or use our free case evaluation form. Speak to a Lawyer Unlike some other law firms, when you call the Law Office of Marta K. Dolvenidze you will speak to an actual attorney. Not a paralegal or assistant. And even after retaining our office you will still speak to an attorney unlike other firms where you cannot get a hold of your attorney after several attempts.</div>

<div class="abs rule" style="top:986px"></div>

<div class="abs card" style="left:40px">
  <h3>Debt Relief</h3>
  <p>Lorem ipsum dolor sit amet, consectetur adipisicing elit, sed do eiusmod tempor incididunt ut labore et dolore magna aliqua. Ut enim ad minim veniam, quis nostrud exercitation ullamco laboris nisi ut aliquip ex ea commodo consequat.</p>
  <span class="btn" style="top:314px">Read More</span>
</div>
<div class="abs card" style="left:326px;height:296px">
  <h3>Foreclosure Prevention</h3>
  <p>Lorem ipsum dolor sit amet, consectetur adipisicing elit, sed do eiusmod tempor incididunt ut labore et dolore magna aliqua. Ut enim ad minim veniam.</p>
  <span class="btn" style="top:270px">Read More</span>
</div>
<div class="abs card" style="left:610px;height:296px">
  <h3>Chapter 13</h3>
  <p>An individual with a regular income who is overcome by debt, but believes such debt can be repaid within a reasonable period of time, may file under chapter 13 of the bankruptcy code.</p>
  <span class="btn" style="top:246px">Read More</span>
</div>
<div class="abs card" style="left:894px;height:340px">
  <h3>Chapter 7</h3>
  <p>Often called the liquidation chapter, or "fresh start," chapter 7 is used by individuals, families, partnerships, or corporations whose financial difficulties do not allow them to repay all of their debts.</p>
  <span class="btn" style="top:290px">Read More</span>
</div>

<div class="abs rule" style="top:1426px"></div>

<div class="abs testi-label">TESTIMONIALS</div>
<div class="abs bar-title testi-title">Excellent Bankruptcy Attorney</div>
<div class="abs text-box testi-text">During our difficult financial times, we pretty much run out of all the possible options. Last option was bankruptcy and it was very difficult to decide on that and to understand what it is all about. It only took 30min with our consultation with Marta, that we really understood what all those chapters are about and understood our options. Before that chapter 7 or 13 were just numbers. Finally it was more clear what we can keep in bankruptcy solution and what we can't. Marta was very patient and made sure we have all of our questions answered before we went to next step. She also gave us materials to read at home. Once we decided to go for it. Ms. Dolvenidze sent us an online form, that was easy to fill out… from their she took care of everything. At court or any meetings we were explained every step. Once again Thank you very Much!!! Marta is very professional, experienced and understanding attorney.</div>

<div class="abs disclaimer">Disclaimer: The Law Offices of Marta K. Dolvenidze is a Debt Relief law firm as defined by 11 U.S.C. 528. We help people file for Bankruptcy Relief under the Bankruptcy Code. The information contained on this website is not to be construed as legal advice. It is not intended to solicit or form an attorney-client relationship. We do not guarantee any result and prior results do not guarantee a similar outcome. This is an attorney advertisement and this website is for informational purposes only.</div>

<div class="abs posts">
  <div class="foot-h">Latest Posts</div>
  <div class="post">Hot off the press! Chirpline buzz surrounding the #StageAwards last night racked in nearly 15m posts!<small>1 day ago</small></div>
  <div class="post">The #StageAwards: A look back via Chirpline <a>http://lnk.example/ab12cd</a><small>1 day ago</small></div>
  <div class="post">Harbor Design Week is underway #hdw. Here's our blog post <a>http://lnk.example/ef34gh</a> and a quick "get started" guide <a>https://lnk.example/ij56kl</a><small>2 days ago</small></div>
  <div class="follow">Follow Me -&gt;</div>
</div>

<div class="abs contact">
  <div class="foot-h" style="margin-bottom:14px">Contact Us Form</div>
  <label>Name:</label><div class="field"></div>
  <label>Email:</label><div class="field"></div>
  <label>Subject:</label><div class="field"></div>
  <label>Your Message:</label><div class="area"></div>
  <span class="btn">Submit</span>
</div>

<div class="abs copyright">© Copyright 2012 Law Office of Marta K. Dolvenidze. All Rights Reserved.</div>

</body>
</html>
```